Business Card Design

WE are looking for a premium quality Business Cards for a Law Firm . Copies of our current business card is attached.

Contact Information for Business Card

xyz

```html
<!DOCTYPE html>
<html lang="en">
<head>
<meta charset="utf-8">
<title>Harcourt Lawyers – Business Cards</title>
<link href="https://fonts.googleapis.com/css2?family=Cinzel:wght@600&family=Arimo:wght@400;700&display=swap" rel="stylesheet">
<style>
  :root {
    --bg: #e4e2de;
    --card: #ffffff;
    --green: #1d3a2b;
    --gold: #b8965a;
    --ink: #3a3a3a;
    --rule: #2b2b2b;
  }
  * { box-sizing: border-box; margin: 0; padding: 0; }
  html, body { width: 1200px; height: 912px; overflow: hidden; }
  body { background: var(--bg); font-family: "Arimo", Arial, sans-serif; color: var(--ink); position: relative; }

  .card {
    position: absolute;
    width: 580px; height: 340px;
    background: var(--card);
    box-shadow: 0 10px 28px rgba(0,0,0,.18);
    overflow: hidden;
  }
  .card--offices { left: 40px; top: 40px; }
  .card--personal { left: 580px; top: 536px; }

  .brand { display: flex; align-items: center; gap: 12px; position: absolute; }
  .brand__dot { width: 34px; height: 34px; border: 3px solid var(--gold); border-radius: 50%; flex: none; }
  .brand__name {
    font-family: "Cinzel", Georgia, serif; font-weight: 600;
    color: var(--green); font-size: 26px; line-height: 1.05; letter-spacing: 1px;
  }
  .card--offices .brand { right: 44px; top: 128px; }
  .card--personal .brand { right: 44px; top: 36px; }

  .offices { position: absolute; left: 44px; top: 38px; font-size: 13.5px; line-height: 1.3; }
  .office { margin-bottom: 14px; }
  .office:last-child { margin-bottom: 0; }
  .office__city { font-weight: 700; color: #111; }
  .office__label { font-weight: 700; color: #111; }

  .divider { position: absolute; left: 44px; right: 44px; top: 118px; border-top: 1px solid var(--rule); }
  .address { position: absolute; right: 44px; top: 132px; text-align: right; font-size: 14px; line-height: 1.3; }

  .person { position: absolute; left: 44px; top: 136px; }
  .person__name { font-family: "Cinzel", Georgia, serif; font-weight: 600; color: var(--green); font-size: 21px; line-height: 1.2; letter-spacing: 1px; }
  .person__role { color: var(--gold); font-size: 13.5px; line-height: 1.3; }
  .person__rule { width: 150px; border-top: 1px solid var(--rule); margin: 7px 0 6px; }

  .contacts { list-style: none; font-size: 13.5px; line-height: 1.45; }
  .contacts li { display: flex; align-items: center; gap: 8px; }
  .contacts svg { width: 12px; height: 12px; fill: var(--green); flex: none; }
</style>
</head>
<body>

<section class="card card--offices" aria-label="Office locations">
  <div class="offices">
    <div class="office">
      <div class="office__city">Melbourne</div>
      <div>Level 12, 48 Flinders Lane</div>
      <div>Melbourne, VIC 3000</div>
      <div><span class="office__label">Phone :</span> +61 03 5550 1842</div>
    </div>
    <div class="office">
      <div class="office__city">Sydney</div>
      <div>Level 9, Harbourview House</div>
      <div>22 Market Street</div>
      <div>Parramatta, NSW 2150</div>
      <div><span class="office__label">Phone :</span> +61 02 5550 3317</div>
    </div>
    <div class="office">
      <div class="office__city">Perth</div>
      <div>Level 21, Terrace Tower</div>
      <div>88 Hay Street</div>
      <div>Perth, WA 6000</div>
      <div><span class="office__label">Phone :</span> +61 08 5550 7260</div>
    </div>
  </div>
  <div class="brand">
    <span class="brand__dot"></span>
    <span class="brand__name">HARCOURT<br>LAWYERS</span>
  </div>
</section>

<section class="card card--personal" aria-label="Personal card">
  <div class="brand">
    <span class="brand__dot"></span>
    <span class="brand__name">HARCOURT<br>LAWYERS</span>
  </div>
  <div class="divider"></div>
  <div class="address">
    <div>Level 3, Harcourt House</div>
    <div>72 Albert Terrace</div>
    <div>Spring Hill, QLD 4000</div>
  </div>
  <div class="person">
    <div class="person__name">DANIEL MERCER</div>
    <div class="person__role">Director &amp; Principal Solicitor</div>
    <div class="person__role">MBA, Juris Doctor</div>
    <div class="person__rule"></div>
    <ul class="contacts">
      <li><svg viewBox="0 0 24 24"><path d="M6.6 10.8a15 15 0 0 0 6.6 6.6l2.2-2.2c.3-.3.7-.4 1-.2 1.1.4 2.3.6 3.6.6.6 0 1 .4 1 1V20c0 .6-.4 1-1 1A17 17 0 0 1 3 4c0-.6.4-1 1-1h3.5c.6 0 1 .4 1 1 0 1.3.2 2.5.6 3.6.1.3 0 .7-.2 1z"/></svg>+61 7 5550 2184</li>
      <li><svg viewBox="0 0 24 24"><path d="M7 1h10a2 2 0 0 1 2 2v18a2 2 0 0 1-2 2H7a2 2 0 0 1-2-2V3a2 2 0 0 1 2-2zm0 3v14h10V4z"/></svg>+61 0491 570 156</li>
      <li><svg viewBox="0 0 24 24"><path d="M2 5h20v14H2zm2 2v.5l8 5 8-5V7z"/></svg>daniel@harcourtlawyers.com.au</li>
      <li><svg viewBox="0 0 24 24"><circle cx="12" cy="12" r="10"/></svg>www.harcourtlawyers.com.au</li>
    </ul>
  </div>
</section>

</body>
</html>
```